Webdesign für Kleingruppenreisen in die Südsteiermark
Zielgruppe
Wir sind ein Start-Up Unternehmen, das als Kleingruppenreisen in die Südsteiermark veranstaltet; der Schwerpunkt liegt auf dem Kulinarischen. Zielgruppe sind Geschäftsleute, die diese Kurzreisen (Do-So) für Marketingzwecke oder als Mitarbeiterbonus (oder auch privat) nutzen möchten.
Aufgabenstellung
Die Homepage soll eine Online-Shop Möglichkeit bieten, in der die Reise (bisher gibt es nur einen Ablauf) gebucht werden kann. Optisch sollte sie sich an das bereits von Ihnen erstellte Logo anlehnen und möglichst ansprechende Fotos von der Südsteiermark, Graz, Leoben usw. enthalten. (Siehe die beiden Flyer und das Logo)
Wir haben inzwischen Bildfreigaben von Haldauer und dem Tourismusverband Kellwinden erhalten und können auch eigene Bilder zur Verfügung stellen. Bitte kontaktieren Sie uns dafür, wenn nötig.

```html
<!DOCTYPE html>
<html lang="de">
<head>
<meta charset="utf-8">
<title>Genusspfad-Reise Südsteiermark</title>
<link rel="stylesheet" href="https://fonts.googleapis.com/css2?family=Open+Sans:ital,wght@0,300;0,400;0,600;0,700;1,300;1,600&family=Great+Vibes&display=swap">
<style>
:root{
  --green:#5d7a36;
  --green-dark:#4d6a2b;
  --green-light:#8aa653;
  --grey-band:#ececec;
  --grey-field:#e9e9e9;
  --grey-crumb:#a5a5a5;
  --text:#333;
  --white:#fff;
}
*{box-sizing:border-box;margin:0;padding:0}
html,body{width:1200px;height:2171px;overflow:hidden;background:var(--white)}
body{position:relative;font-family:"Open Sans",Arial,sans-serif;color:var(--text)}
.abs{position:absolute}
.photo{position:absolute}
/* header */
.header-photo{left:0;top:0;width:1200px;height:205px;background:linear-gradient(90deg,#3f5a22 0%,#7d9c3f 30%,#a4bb5e 55%,#6d8e33 80%,#4a6a25 100%)}
.header-shadow{left:0;top:203px;width:1200px;height:3px;background:#c9c9c9}
.logo-box{left:225px;top:2px;width:244px;height:143px;background:var(--white);display:flex;align-items:center;justify-content:center;gap:8px}
.logo-box .dot{width:16px;height:16px;border-radius:50%;background:var(--green)}
.logo-box span{font-size:22px;font-weight:700;color:var(--green)}
.nav{left:469px;top:88px;width:491px;height:37px;background:var(--green);display:flex;align-items:center;padding-left:85px;gap:15px}
.nav a{color:var(--white);font-size:11.5px;font-weight:600;text-decoration:none}
/* breadcrumb */
.crumbs{left:225px;top:250px;height:22px;display:flex}
.crumb{height:22px;display:flex;align-items:center;padding:0 14px 0 18px;font-size:6px;font-weight:600;color:var(--white);background:var(--grey-crumb);clip-path:polygon(0 0,calc(100% - 7px) 0,100% 50%,calc(100% - 7px) 100%,0 100%,7px 50%);margin-right:2px}
.crumb.home{padding:0 14px;clip-path:polygon(0 0,calc(100% - 7px) 0,100% 50%,calc(100% - 7px) 100%,0 100%)}
.crumb.active{background:var(--green)}
.title{left:0;top:290px;width:1200px;text-align:center;font-family:"Great Vibes",cursive;font-size:44px;font-weight:400;color:var(--green)}
.divider{left:540px;top:350px;width:120px;height:18px}
/* product */
.product-photo{left:225px;top:390px;width:256px;height:257px;background:linear-gradient(160deg,#7c9a4a 0%,#5b6b3c 40%,#5a4630 70%,#3d2f22 100%);box-shadow:0 1px 4px rgba(0,0,0,.35)}
.price{left:528px;top:385px;font-size:24px;font-weight:300;color:var(--green)}
.fine{left:530px;font-size:6px;color:#777}
.fine.meta{color:var(--green-light)}
.stars{left:881px;top:394px;display:flex;gap:2px}
.rating{left:881px;top:410px;font-size:11px;color:var(--text)}
.field{left:531px;width:180px;height:31px;background:var(--grey-field);display:flex;align-items:center;justify-content:space-between;padding:0 8px 0 10px;font-size:11px;font-style:italic;font-weight:300;color:#888}
.btn-book{left:531px;top:570px;width:104px;height:31px;background:var(--green);color:var(--white);font-size:14.5px;display:flex;align-items:center;justify-content:center}
.wishlist{left:529px;top:628px;display:flex;align-items:center;gap:5px;font-size:11px}
.share{left:733px;top:626px;display:flex;gap:10px}
.share i{display:block;width:22px;height:22px;border-radius:50%;background:#555}
.intro{left:225px;top:668px;width:760px;font-size:11px;line-height:13.6px;color:#222}
.intro p{margin-bottom:13px}
/* gallery */
.band{left:0;top:861px;width:1200px;height:573px;background:var(--grey-band)}
.more{left:225px;top:1252px;width:244px;height:182px;background:var(--green);padding:36px 14px 0;color:var(--white)}
.more h3{font-size:18px;font-weight:400;line-height:23px}
.more a{display:block;margin-top:22px;border:1px solid var(--white);height:38px;line-height:36px;padding-left:8px;font-size:15px;color:var(--white);text-decoration:none}
.badge{left:179px;top:827px;width:130px;height:130px}
/* cta */
.cta{left:0;top:1492px;width:1200px;height:293px;background:radial-gradient(ellipse at 40% 45%,#8aa560 0%,#6f8c44 55%,#5c7a35 100%);border-top:2px solid #9a9a9a}
.cta h2{position:absolute;left:229px;top:37px;font-size:30px;font-style:italic;font-weight:600;line-height:36px;color:var(--white)}
.cta p{position:absolute;left:229px;top:148px;font-size:23px;font-weight:300;line-height:27px;color:var(--white)}
.cta a{position:absolute;left:693px;top:193px;width:287px;height:43px;border:1px solid var(--white);color:var(--white);font-size:23px;font-style:italic;font-weight:600;text-align:center;line-height:41px;text-decoration:none}
/* footer */
.hills{left:0;top:1846px;width:660px;height:123px}
.footer{left:0;top:1968px;width:1200px;height:203px;background:var(--green);color:var(--white)}
.footer .brand{position:absolute;left:247px;top:36px;font-size:13px;font-weight:700}
.footer .addr{position:absolute;left:247px;top:51px;font-size:11px;line-height:13.5px}
.footer .phone{position:absolute;left:247px;top:101px;font-size:11px;line-height:13.5px}
.footer .col{position:absolute;top:36px;font-size:11px;line-height:22px;font-weight:300}
.footer .col b{font-weight:700}
.footer .social{position:absolute;left:737px;top:42px;display:flex;gap:13px}
.footer .social span{display:flex;align-items:center;justify-content:center;width:50px;height:50px;border-radius:50%;background:var(--white);color:var(--green);font-size:8.5px;font-weight:700}
.footer .rule{position:absolute;left:225px;top:154px;width:750px;height:1px;background:rgba(255,255,255,.7)}
.footer .copy{position:absolute;left:0;top:166px;width:1200px;text-align:center;font-size:11px;font-weight:300}
</style>
</head>
<body>

<div class="abs photo header-photo" role="img" aria-label="Weinberge der Südsteiermark mit Trauben im Vordergrund"></div>
<div class="abs header-shadow"></div>
<div class="abs logo-box"><i class="dot"></i><span>Genusspfad Reisen</span></div>
<nav class="abs nav">
  <a href="#">Startseite</a><a href="#">Jetzt buchen</a><a href="#">Shop</a><a href="#">Kontakt</a><a href="#">Ein Menüpunkt</a>
</nav>

<div class="abs crumbs">
  <div class="crumb home"><svg width="12" height="11" viewBox="0 0 12 11"><path d="M6 0L0 5h1.5v6h3.5V7.5h2V11h3.5V5H12z" fill="#fff"/></svg></div>
  <div class="crumb">Breadcrumb</div>
  <div class="crumb active">Genusspfad-Reise Südsteiermark</div>
</div>

<h1 class="abs title">Genusspfad-Reise Südsteiermark</h1>
<svg class="abs divider" viewBox="0 0 120 18"><line x1="0" y1="9" x2="48" y2="9" stroke="#555" stroke-width="1"/><line x1="72" y1="9" x2="120" y2="9" stroke="#555" stroke-width="1"/><circle cx="60" cy="9" r="7" fill="#7d9c3f"/></svg>

<div class="abs photo product-photo" role="img" aria-label="Weinglas auf Holztisch im Weinberg mit Trauben und Walnüssen"></div>
<div class="abs price">1.650,00 €*</div>
<div class="abs fine" style="top:415px">inkl. MwSt. zzgl. Versandkosten</div>
<div class="abs fine meta" style="top:428px">Kategorie: Südsteiermark</div>
<div class="abs fine meta" style="top:437px">Artikelnummer: 03-18</div>
<div class="abs stars">
  <svg width="94" height="16" viewBox="0 0 94 16" fill="#4d6a2b"><defs><path id="st" d="M8 0l2.4 5.2 5.6.6-4.2 3.8 1.2 5.6L8 12.4 3 15.2l1.2-5.6L0 5.8l5.6-.6z"/></defs><use href="#st"/><use href="#st" x="19.5"/><use href="#st" x="39"/><use href="#st" x="58.5"/><use href="#st" x="78"/></svg>
</div>
<div class="abs rating">(32 Bewertungen)</div>
<div class="abs field" style="top:476px">Wählen Sie Ihren Reisetermin
  <svg width="20" height="20" viewBox="0 0 20 20"><rect x="2" y="4" width="16" height="14" rx="1.5" fill="none" stroke="#666" stroke-width="1.8"/><rect x="2" y="4" width="16" height="4" fill="#666"/><path d="M6 2v4M14 2v4" stroke="#666" stroke-width="1.8"/><path d="M6.5 12.5l2.5 2.5 4.5-5" fill="none" stroke="#666" stroke-width="1.8"/></svg>
</div>
<div class="abs field" style="top:523px">Personenanzahl
  <svg width="18" height="14" viewBox="0 0 18 14" fill="#666"><circle cx="9" cy="4" r="3"/><circle cx="3.5" cy="5" r="2.2"/><circle cx="14.5" cy="5" r="2.2"/><path d="M3 14c0-4 2.7-6 6-6s6 2 6 6z"/><path d="M0 13c0-3 1.5-4.5 3.5-4.5S6 10 6 13zM12 13c0-3 1.5-4.5 2.5-4.5S18 10 18 13z"/></svg>
</div>
<div class="abs btn-book">Jetzt buchen</div>
<div class="abs wishlist"><svg width="19" height="16" viewBox="0 0 19 16"><path d="M9.5 16L1.5 8A4.5 4.5 0 0 1 9.5 2 4.5 4.5 0 0 1 17.5 8z" fill="#555"/></svg>Zur Merkliste hinzufügen</div>
<div class="abs share"><i></i><i></i><i></i><i></i></div>

<div class="abs intro">
  <p>Lernen Sie Leoben, die Hauptstadt des Haldauer-Bieres kennen&nbsp; und erfahren Sie im Haldeum die Geschichte dieses weltbekannten Gebräus.</p>
  <p>Entdecken Sie Graz, die ab-wechslungsreiche Landeshauptstadt und Kulturhauptstadt 2003, mit ihren vielfältigen kulturellen Angeboten, den charmanten Gassen und atem-beraubenden&nbsp; Ausblicken. Genießen Sie die südlichere Sonne und kosten Sie die ausgezeichneten Weine der Winzer in der Buschenschank.</p>
  <p>Während unser Exklusiv Transfer Sie zu den Sehenswürdigkeiten bringt, lüftet unser steirischer Reiseleiter für Sie die Geheimnisse seines Heimatlandes, des „grünen Herzens Österreichs“ und führt Sie in erstklassige Restaurants. Sie wohnen in ausgesuchten Hotels in zentraler Lage.</p>
</div>

<div class="abs band"></div>
<div class="photo" style="left:225px;top:861px;width:244px;height:378px;background:linear-gradient(180deg,#c9d3c8 0%,#6f9140 35%,#3f5a28 70%,#5d8233 100%)" role="img" aria-label="Blaue Trauben am Rebstock mit Weinberg im Hintergrund"></div>
<div class="photo" style="left:481px;top:861px;width:238px;height:182px;background:linear-gradient(180deg,#3f86d2 0%,#6ea7e0 55%,#b86a4a 72%,#4f7a32 100%)" role="img" aria-label="Klapotetz auf einem Hausdach vor blauem Himmel"></div>
<div class="photo" style="left:731px;top:861px;width:244px;height:182px;background:linear-gradient(180deg,#4e8fd8 0%,#d98a55 35%,#c74a36 65%,#7a6a58 100%)" role="img" aria-label="Bunte Häuserfassaden am Hauptplatz in Graz mit Brunnen"></div>
<div class="photo" style="left:481px;top:1057px;width:341px;height:182px;background:linear-gradient(180deg,#e9c98d 0%,#f2d49a 35%,#8a8a4a 60%,#4d6a2c 100%)" role="img" aria-label="Klapotetz vor Weinberghügeln im Sonnenuntergang"></div>
<div class="photo" style="left:836px;top:1057px;width:139px;height:182px;background:linear-gradient(90deg,#4c8fdc 0%,#d9b960 45%,#e1c77a 60%,#3f6a2e 100%)" role="img" aria-label="Gelbe Kapelle mit Kirchturm vor blauem Himmel"></div>
<div class="photo" style="left:481px;top:1252px;width:139px;height:182px;background:linear-gradient(180deg,#3a3833 0%,#6d6a55 40%,#d8df6a 60%,#3c3a35 100%)" role="img" aria-label="Beleuchteter Biertank in einer Brauereiausstellung"></div>
<div class="photo" style="left:634px;top:1252px;width:341px;height:182px;background:linear-gradient(160deg,#9aa1a8 0%,#b9bcbf 30%,#6d7a5a 60%,#7a6a3d 100%)" role="img" aria-label="Wanderer in einer alpinen Berglandschaft"></div>
<div class="abs more">
  <h3>Sie möchten mehr Impressionen?</h3>
  <a href="#">Alle Impressionen anzeigen</a>
</div>
<svg class="abs badge" viewBox="0 0 130 130">
  <circle cx="65" cy="65" r="64" fill="#5d7a36"/>
  <circle cx="65" cy="65" r="56" fill="none" stroke="#fff" stroke-width="1.2"/>
  <g transform="rotate(-18 65 65)" fill="#fff" font-family="Open Sans, sans-serif" text-anchor="middle">
    <text x="65" y="54" font-size="8" font-weight="600" textLength="86" lengthAdjust="spacingAndGlyphs">Eine kulinarische Reise</text>
    <text x="65" y="68" font-size="11" font-weight="700" textLength="96" lengthAdjust="spacingAndGlyphs">mit sensationellen</text>
    <text x="65" y="81" font-size="10" font-weight="700" textLength="92" lengthAdjust="spacingAndGlyphs">Sehenswürdigkeiten</text>
  </g>
</svg>

<section class="abs cta" role="img" aria-label="Weiße Weintrauben am Rebstock, grün eingefärbt">
  <h2>Erleben Sie die<br>gastronomische Vielfalt der Süd-Steiermark</h2>
  <p>Sie suchen ein bestimmtes Gaumenerlebnis?<br>Dann helfen wir Ihnen gerne weiter.</p>
  <a href="#">Jetzt beraten lassen</a>
</section>

<svg class="abs hills" viewBox="0 0 660 123" role="img" aria-label="Silhouette einer steirischen Berglandschaft mit Ortschaft">
  <path d="M0 123V70C60 50 110 20 170 8 220 0 280 20 340 40 400 55 470 70 540 85 600 98 640 112 660 123z" fill="#5d7a36"/>
</svg>

<footer class="abs footer">
  <svg class="abs" style="left:225px;top:37px" width="11" height="15" viewBox="0 0 11 15"><path d="M5.5 0A5.5 5.5 0 0 0 0 5.5C0 9.5 5.5 15 5.5 15S11 9.5 11 5.5A5.5 5.5 0 0 0 5.5 0zm0 8A2.5 2.5 0 1 1 5.5 3a2.5 2.5 0 0 1 0 5z" fill="#fff"/></svg>
  <div class="brand">Genusspfad Reisen</div>
  <div class="addr">Marlene Hollberg<br>Lindenweg 12<br>D - 10999 Berlin</div>
  <svg class="abs" style="left:225px;top:103px" width="13" height="13" viewBox="0 0 13 13"><path d="M2.6 0l2.2 3-1.3 1.6c.8 1.8 2.1 3.1 3.9 3.9L9 7.2l3 2.2-1 2.6C5.5 12.6.4 7.5 0 1z" fill="#fff"/></svg>
  <div class="phone">Deutschland: +49 170 0000 318<br>Österreich: +43 681 0000 4127</div>
  <div class="col" style="left:460px"><b>MENÜ</b><br>MENÜPUNKT<br>MENÜPUNKT<br>MENÜPUNKT<br>MENÜPUNKT</div>
  <div class="col" style="left:599px"><b>MENÜ</b><br>MENÜPUNKT<br>MENÜPUNKT<br>MENÜPUNKT<br>MENÜPUNKT</div>
  <div class="social"><span>Plauder</span><span>Filmo</span><span>Kreisel</span><span>Zwitscha</span></div>
  <div class="rule"></div>
  <div class="copy">© 2017. Agentur Kremling</div>
</footer>

</body>
</html>
```